MV Personal Name/Business Card.

I need a double-sided name card with a logo/full design incorporating the "themes/concepts" of:
Neurology, wellness, Animals, Healing, Chiropractic, lifestyle, energy, creatvity & color on both sides of the card.
Information to include:
Name: Miranda Voss
Mobile #: 0471 862 913
Email chiromvh@pelomail.com

Possible use of "MV Health & Chiropractic"

Target Market(s)

People of all ages looking to improve their health & lifestyle.

Industry/Entity Type

Business

```html
<!DOCTYPE html>
<html lang="en">
<head>
<meta charset="utf-8">
<title>MV Health &amp; Chiropractic – Business Card</title>
<link rel="stylesheet" href="https://fonts.googleapis.com/css2?family=Open+Sans:wght@400;700&family=Quicksand:wght@300;400&display=swap">
<style>
  :root {
    --page: #e9e7e3;
    --card-white: #f7f7f6;
    --ink-grey: #5c5f63;
    --accent-orange: #e6982a;
    --dark-slate: #262a2f;
    --dark-slate-light: #3b4047;
    --back-text: #d9dadc;
  }
  * { margin: 0; padding: 0; box-sizing: border-box; }
  html, body { width: 1200px; height: 676px; overflow: hidden; background: var(--page); }
  .canvas {
    width: 1200px; height: 676px;
    display: flex; align-items: center; justify-content: center; gap: 60px;
  }
  .card {
    width: 520px; height: 297px; position: relative; overflow: hidden;
    box-shadow: 0 6px 18px rgba(0,0,0,.18);
  }
  .card-front { background: var(--card-white); font-family: "Open Sans", sans-serif; }
  .front-shapes { position: absolute; inset: 0; }
  .contact-block {
    position: absolute; right: 44px; top: 92px; text-align: right;
  }
  .holder-name { font-size: 23px; font-weight: 700; color: var(--ink-grey); line-height: 1.1; }
  .practice-name { font-size: 12.5px; color: var(--accent-orange); margin-top: 2px; }
  .contact-line {
    display: flex; justify-content: flex-end; align-items: center; gap: 7px;
    font-size: 12.5px; color: var(--ink-grey); margin-top: 6px;
  }
  .contact-line:first-of-type { margin-top: 14px; }
  .contact-icon { width: 13px; height: 13px; flex: none; }
  .front-website {
    position: absolute; right: 30px; bottom: 20px;
    font-size: 15px; font-weight: 700; color: #fff; letter-spacing: .2px;
  }
  .card-back {
    background: linear-gradient(135deg, var(--dark-slate-light) 0%, var(--dark-slate) 55%, #1d2024 100%);
    font-family: "Quicksand", sans-serif;
    display: flex; flex-direction: column; justify-content: center; align-items: center;
    text-align: center;
  }
  .themes { font-size: 17px; font-weight: 300; color: var(--back-text); line-height: 1.45; letter-spacing: .3px; }
  .back-website { font-size: 16px; font-weight: 400; color: var(--accent-orange); margin-top: 16px; letter-spacing: .3px; }
</style>
</head>
<body>
<main class="canvas">
  <section class="card card-front" aria-label="Card front">
    <svg class="front-shapes" viewBox="0 0 520 297" width="520" height="297" aria-hidden="true">
      <path d="M0 188 L330 236 L330 297 L0 224 Z" fill="var(--accent-orange)"/>
      <path d="M0 224 L330 297 L0 297 Z" fill="var(--card-white)"/>
      <path d="M238 297 Q282 238 372 232 L520 232 L520 297 Z" fill="var(--dark-slate)"/>
    </svg>
    <div class="contact-block">
      <div class="holder-name">Miranda Voss</div>
      <div class="practice-name">MV Health &amp; Chiropractic</div>
      <div class="contact-line">0471 862 913
        <svg class="contact-icon" viewBox="0 0 14 14" aria-hidden="true"><rect x="3" y="1" width="8" height="12" rx="1.5" fill="none" stroke="var(--accent-orange)" stroke-width="1.5"/><rect x="6" y="10.5" width="2" height="1" fill="var(--accent-orange)"/></svg>
      </div>
      <div class="contact-line">chiromvh@pelomail.com
        <svg class="contact-icon" viewBox="0 0 14 14" aria-hidden="true"><rect x="1" y="3" width="12" height="8" fill="var(--accent-orange)"/><path d="M1 3 L7 8 L13 3" fill="none" stroke="#fff" stroke-width="1.2"/></svg>
      </div>
    </div>
    <div class="front-website">www.mvwellnesscare.com</div>
  </section>

  <section class="card card-back" aria-label="Card back">
    <p class="themes">Neurology | Wellness | Animals | Healing | Chiropractic<br>Lifestyle | Energy | Creatvity &amp; color on both sides.</p>
    <p class="back-website">www.mvwellnesscare.net</p>
  </section>
</main>
</body>
</html>
```